sydney wedding photography business needs a business card design

we need a business card design for a sydney based wedding photography and videography business. our business name is :golden hour studio and film. our target clients are 24-35 yrs female. our style is candid, organic, natural, dynamic. we are a team of young photographers and videographers, and help brides to create memories that they will cherish for the rest of their lives. the logo will be provided. we want an elegant design that reflects our style, and also want to give a great impression to our clients that we are one of the best studios in sydney and our brand means quality and premium service.

Target Market(s)

bride to be, 24-35 years old, living in sydney and surrunding areas

Industry/Entity Type

Wedding Photography

Contact Information for Business Card

address: 57 tarrant street, glenmore nsw 2047
mobile: 0431872259
phone: (02) 9163 2408
info@tidewillowstudio.net.au
www.tidewillowstudio.net.au
facebook:tidewillowweddings
instagram:tidewillowweddings

Font styles to use
Serif
Sans Serif

Requirements
Nice to have
• maybe add my slogan"memories beyond eternity" if the layout looks good
Should not have
• no black color, not good idea for wedding biz card

```html
<!DOCTYPE html>
<html lang="en">
<head>
<meta charset="utf-8">
<title>Golden Hour Studio and Film — Business Card</title>
<link rel="stylesheet" href="https://fonts.googleapis.com/css2?family=Dancing+Script:wght@700&family=Source+Sans+3:wght@400;600&display=swap">
<style>
  :root {
    --backdrop-top: #2a2a2a;
    --backdrop-bottom: #050505;
    --card-white: #ffffff;
    --gold: #dcaa08;
    --gold-light: #f3c300;
    --gold-deep: #c8930e;
    --ink: #333333;
    --white: #ffffff;
  }
  * { margin: 0; padding: 0; box-sizing: border-box; }
  html, body {
    width: 1200px; height: 900px; overflow: hidden;
  }
  body {
    position: relative;
    background: linear-gradient(180deg, var(--backdrop-top) 0%, #1a1a1a 55%, var(--backdrop-bottom) 100%);
    font-family: "Source Sans 3", "Helvetica Neue", Arial, sans-serif;
  }
  .card {
    position: absolute;
    top: 170px;
    width: 347px;
    height: 561px;
    overflow: hidden;
  }
  .card--front { left: 259px; background: var(--card-white); }
  .card--back {
    left: 631px;
    background: radial-gradient(ellipse 75% 60% at 50% 48%, var(--gold-light) 0%, #e4b300 55%, var(--gold-deep) 100%);
  }
  .tab {
    position: absolute;
    left: 102px;
    width: 143px;
    background: linear-gradient(180deg, var(--gold-deep), var(--gold-light));
  }
  .tab--top { top: 0; height: 30px; background: linear-gradient(180deg, var(--gold-light), var(--gold-deep)); }
  .tab--bottom { bottom: 0; height: 28px; }

  .brand-name {
    position: absolute;
    left: 0; right: 0;
    text-align: center;
    font-weight: 600;
    text-transform: uppercase;
    letter-spacing: 4px;
    line-height: 1.25;
  }
  .brand-name__line { display: block; }
  .card--front .brand-name {
    top: 142px;
    color: var(--gold);
    font-size: 21px;
  }
  .card--back .brand-name {
    top: 252px;
    color: var(--white);
    font-size: 23px;
  }

  .contact {
    position: absolute;
    left: 0; right: 0;
    top: 302px;
    text-align: center;
    color: var(--ink);
    font-size: 14.5px;
    line-height: 21px;
  }
  .contact__name {
    font-family: "Dancing Script", "Brush Script MT", cursive;
    font-weight: 700;
    font-size: 36px;
    line-height: 40px;
    color: var(--gold);
  }
  .contact__role { margin-bottom: 20px; }
  .contact__lines { margin-bottom: 16px; }
  .contact__address { line-height: 17px; }

  .brand-echo {
    position: absolute;
    left: 50%; top: 50%;
    transform: translate(-50%, -50%) rotate(-60deg);
    white-space: nowrap;
    font-weight: 600;
    font-size: 46px;
    letter-spacing: 8px;
    text-transform: uppercase;
    color: rgba(160, 110, 0, 0.13);
  }
</style>
</head>
<body>
  <section class="card card--front" aria-label="Business card front">
    <div class="tab tab--top"></div>
    <h1 class="brand-name">
      <span class="brand-name__line">Golden Hour</span>
      <span class="brand-name__line">Studio and Film</span>
    </h1>
    <div class="contact">
      <p class="contact__name">Olivia Hart</p>
      <p class="contact__role">Managing Director</p>
      <p class="contact__lines">
        0431 872 259<br>
        info@tidewillowstudio.net.au<br>
        www.tidewillowstudio.net.au
      </p>
      <p class="contact__address">
        57 Tarrant Street<br>
        Glenmore NSW 2047
      </p>
    </div>
    <div class="tab tab--bottom"></div>
  </section>

  <section class="card card--back" aria-label="Business card back">
    <div class="brand-echo" aria-hidden="true">Golden Hour</div>
    <p class="brand-name">
      <span class="brand-name__line">Golden Hour</span>
      <span class="brand-name__line">Studio and Film</span>
    </p>
  </section>
</body>
</html>
```